I need a business card design for a new business based in South West Australia.
I specialize in residential window cleaning & general handyman maintenance.

Dale Marsh - 412 SILVER HAWK DETAILING
- Window Cleaning
- House Maintenance

```html
<!DOCTYPE html>
<html lang="en">
<head>
<meta charset="utf-8">
<title>412 Silver Hawk Detailing – Business Card</title>
<link rel="stylesheet" href="https://fonts.googleapis.com/css2?family=Arimo:wght@400&family=Tinos:wght@400;700&display=swap">
<style>
  :root {
    --page-bg: #d9d4cc;
    --card-deep: #04121c;
    --card-mid: #0c2c40;
    --card-glow: #1f6585;
    --text-light: #eef2f4;
    --text-soft: #d7dde0;
    --icon-ring: #c9d0d4;
  }
  * { margin: 0; padding: 0; box-sizing: border-box; }
  html, body {
    width: 1200px;
    height: 892px;
    overflow: hidden;
    background: var(--page-bg);
  }
  .canvas {
    position: relative;
    width: 1200px;
    height: 892px;
  }
  .business-card {
    position: absolute;
    left: 75px;
    top: 146px;
    width: 1050px;
    height: 600px;
    border-radius: 34px;
    overflow: hidden;
    box-shadow: 0 18px 40px rgba(0, 0, 0, 0.35);
  }
  .card-backdrop {
    position: absolute;
    inset: 0;
    background:
      radial-gradient(ellipse 60% 55% at 42% 22%, var(--card-glow) 0%, rgba(31, 101, 133, 0) 70%),
      linear-gradient(160deg, var(--card-mid) 0%, var(--card-deep) 75%);
  }
  .squeegee-area {
    position: absolute;
    left: 560px;
    top: 380px;
    width: 330px;
    height: 220px;
    background: radial-gradient(ellipse at 50% 70%, rgba(70, 80, 88, 0.55) 0%, rgba(4, 18, 28, 0) 70%);
  }
  .card-content {
    position: relative;
    height: 100%;
    text-align: center;
    color: var(--text-light);
  }
  .company-name {
    position: absolute;
    top: 64px;
    left: 0;
    right: 0;
    font-family: "Arimo", Arial, sans-serif;
    font-weight: 400;
    font-size: 50px;
    letter-spacing: 1px;
  }
  .tagline {
    position: absolute;
    top: 132px;
    left: 0;
    right: 0;
    font-family: "Tinos", "Times New Roman", serif;
    font-size: 27px;
    color: var(--text-soft);
  }
  .owner-name {
    position: absolute;
    top: 220px;
    left: 0;
    right: 0;
    font-family: "Tinos", "Times New Roman", serif;
    font-weight: 700;
    font-size: 64px;
    letter-spacing: 1px;
  }
  .service-list {
    position: absolute;
    top: 340px;
    left: 470px;
    list-style: none;
    text-align: left;
    font-family: "Arimo", Arial, sans-serif;
    font-size: 36px;
  }
  .service-item {
    display: flex;
    align-items: center;
    gap: 18px;
    height: 62px;
  }
  .service-icon { width: 24px; height: 24px; flex: none; }
</style>
</head>
<body>
<main class="canvas">
  <article class="business-card">
    <div class="card-backdrop" role="img" aria-label="Dark blue glass with water droplets"></div>
    <div class="squeegee-area" role="img" aria-label="Window squeegee wiping wet glass"></div>
    <div class="card-content">
      <h1 class="company-name">412 SILVER HAWK DETAILING</h1>
      <p class="tagline">residential window cleaning &amp; general handyman maintenance</p>
      <h2 class="owner-name">Dale Marsh</h2>
      <ul class="service-list">
        <li class="service-item">
          <svg class="service-icon" viewBox="0 0 24 24" aria-hidden="true">
            <circle cx="12" cy="12" r="9" fill="none" stroke="var(--icon-ring)" stroke-width="2"/>
            <circle cx="12" cy="12" r="3.5" fill="var(--icon-ring)"/>
          </svg>
          <span>Window Cleaning</span>
        </li>
        <li class="service-item">
          <svg class="service-icon" viewBox="0 0 24 24" aria-hidden="true">
            <circle cx="12" cy="12" r="9" fill="none" stroke="var(--icon-ring)" stroke-width="2"/>
            <circle cx="12" cy="12" r="3.5" fill="var(--icon-ring)"/>
          </svg>
          <span>House Maintenance</span>
        </li>
      </ul>
    </div>
  </article>
</main>
</body>
</html>
```